Professional & attention grabbing.

A business card design, front and back. I already have a logo I will attach, but I am open to something new as well.
Things to include:
Name:
Title:
Phone:
Email:
Wanting something that is professional but attention grabbing.
Also we do a lot of work using drones on natural gas pipelines (leading the future)if you want to include any of that. I'm open to ideas.
Target Market(s)
Natural gas transmission industry / greenhouse gas mitigation industry
Industry/Entity Type
Business
Colors
Designer to choose colors to be used in the design.
Look and feel
Each slider illustrates characteristics of the customer's brand and the style your logo design should communicate.

```html
<!DOCTYPE html>
<html lang="en">
<head>
<meta charset="utf-8">
<title>KV Field Inspections – Business Card</title>
<link rel="stylesheet" href="https://fonts.googleapis.com/css2?family=Roboto:wght@400;500;700&family=Roboto+Condensed:wght@400;700&display=swap">
<style>
  :root {
    --canvas-bg: #d9d9db;
    --card-dark: #2a2a2d;
    --card-dark-deep: #1c1c1e;
    --card-light: #ffffff;
    --brand-red: #d9211f;
    --text-light: #ffffff;
    --text-dark: #333336;
    --text-muted: #555558;
  }
  * { margin: 0; padding: 0; box-sizing: border-box; }
  html, body { width: 1200px; height: 852px; overflow: hidden; }
  body {
    background: var(--canvas-bg);
    font-family: "Roboto", Arial, sans-serif;
    display: flex;
    align-items: center;
    justify-content: center;
    gap: 40px;
  }
  .card {
    position: relative;
    width: 520px;
    height: 300px;
    border-radius: 14px;
    overflow: hidden;
    box-shadow: 0 10px 30px rgba(0,0,0,.25);
  }

  /* Front */
  .card-front {
    background: linear-gradient(135deg, #3a3a3e 0%, var(--card-dark) 45%, var(--card-dark-deep) 100%);
  }
  .front-band {
    position: absolute;
    left: 298px; right: 0;
    top: 152px;
    height: 12px;
    background: var(--brand-red);
  }
  .tagline-band {
    position: absolute;
    left: 0; right: 0;
    bottom: 34px;
    height: 34px;
    background: var(--brand-red);
    display: flex;
    align-items: center;
    justify-content: center;
  }
  .tagline {
    color: var(--text-light);
    font-size: 14px;
    letter-spacing: .3px;
  }

  .wordmark {
    display: flex;
    align-items: center;
    gap: 10px;
    color: var(--text-light);
    font-family: "Roboto Condensed", Arial, sans-serif;
    font-weight: 700;
  }
  .wordmark-square {
    width: 30px; height: 30px;
    background: var(--brand-red);
    flex: none;
  }
  .wordmark-text { display: flex; flex-direction: column; line-height: 1; }
  .wordmark-main { font-size: 58px; letter-spacing: -1px; }
  .wordmark-sub { font-size: 12px; letter-spacing: 1.2px; margin-top: 4px; white-space: nowrap; }
  .card-front .wordmark {
    position: absolute;
    left: 120px;
    top: 96px;
  }

  /* Back */
  .card-back { background: var(--card-light); }
  .back-panel { position: absolute; inset: 0; }
  .card-back .wordmark {
    position: absolute;
    left: 95px;
    top: 160px;
    transform: translate(-50%, -50%) rotate(-90deg);
  }
  .card-back .wordmark-main { font-size: 52px; }
  .contact-block {
    position: absolute;
    left: 262px;
    top: 86px;
  }
  .person-name {
    color: var(--brand-red);
    font-weight: 700;
    font-size: 22px;
    letter-spacing: 1px;
  }
  .person-title {
    color: var(--text-muted);
    font-size: 13px;
    margin-top: 3px;
  }
  .contact-list { list-style: none; margin-top: 22px; }
  .contact-item {
    display: flex;
    align-items: center;
    gap: 10px;
    color: var(--text-dark);
    font-size: 14px;
    margin-bottom: 6px;
  }
  .contact-icon { width: 13px; height: 13px; fill: var(--brand-red); flex: none; }
</style>
</head>
<body>

  <section class="card card-front" aria-label="Card front">
    <div class="front-band"></div>
    <div class="wordmark">
      <span class="wordmark-square"></span>
      <span class="wordmark-text">
        <span class="wordmark-main">KV</span>
        <span class="wordmark-sub">FIELD INSPECTIONS</span>
      </span>
    </div>
    <div class="tagline-band">
      <p class="tagline">Also we do a lot of work using drones on natural gas pipelines</p>
    </div>
  </section>

  <section class="card card-back" aria-label="Card back">
    <svg class="back-panel" viewBox="0 0 520 300" preserveAspectRatio="none" aria-hidden="true">
      <defs>
        <linearGradient id="panelShade" x1="0" y1="0" x2="1" y2="1">
          <stop offset="0" stop-color="#3a3a3e"/>
          <stop offset="1" stop-color="#1c1c1e"/>
        </linearGradient>
      </defs>
      <path d="M0 0 H150 C235 60 250 190 210 300 H0 Z" fill="var(--brand-red)"/>
      <path d="M0 0 H140 C222 60 236 190 198 300 H0 Z" fill="url(#panelShade)"/>
    </svg>

    <div class="wordmark">
      <span class="wordmark-square"></span>
      <span class="wordmark-text">
        <span class="wordmark-main">KV</span>
        <span class="wordmark-sub">FIELD INSPECTIONS</span>
      </span>
    </div>

    <div class="contact-block">
      <h1 class="person-name">DANIEL REEVE</h1>
      <p class="person-title">Managing Director</p>
      <ul class="contact-list">
        <li class="contact-item">
          <svg class="contact-icon" viewBox="0 0 16 16" aria-hidden="true"><path d="M3.6 1.2l2.3 2.6-1.4 1.7c.9 2 2.4 3.5 4.4 4.4l1.7-1.4 2.6 2.3-1.3 2.2C6.5 13 3 9.5 1.4 2.5z"/></svg>
          <span>1300 555 018</span>
        </li>
        <li class="contact-item">
          <svg class="contact-icon" viewBox="0 0 16 16" aria-hidden="true"><circle cx="8" cy="8" r="7"/><path d="M1 8h14M8 1c3 3 3 11 0 14M8 1c-3 3-3 11 0 14" stroke="#fff" stroke-width="1.2" fill="none"/></svg>
          <span>www.kvfield.example</span>
        </li>
        <li class="contact-item">
          <svg class="contact-icon" viewBox="0 0 16 16" aria-hidden="true"><rect x="1" y="3" width="14" height="10" rx="1"/><path d="M1.5 3.8L8 9l6.5-5.2" stroke="#fff" stroke-width="1.3" fill="none"/></svg>
          <span>daniel.reeve@kvfield.example</span>
        </li>
      </ul>
    </div>
  </section>

</body>
</html>
```